Music Studio and Store Business Card and Logo Design

We need a business card and logo design for an existing Music Studio (Piano and Voice) which will soon expand to offer retail sheet music for all instruments including voice. The expanding store will not sell or lease instruments. We are a well known Fine Arts Studio for instruction to children, college students, and adults with 42 enrolled students and a wait list. We want something with simple elegance, but not archaic. Even a sleek modern look is okay. We do not want something childish or too fun looking because we do serve ages 5 - 62. We would also like the logo workable/transferable to signage for our new location opening in March. We like classic burgundy, black, deep blues, but are open to other suggestions. We included our studio brochure so you can get to know us a little better and some images we thought were interesting with the use of clef signs for the & and using note heads for the bottom or top of the letter "H"

Target Market(s)

All ages

Industry/Entity Type

Business

Contact Information for Business Card

H&H Music StudioPlattsburgh, NYWanda J. Haby and Oren M. Castaldi, Owners

Requirements
Must have
• Phone Number: (555) 817-4062
• Website: www.rbtonalartsroom.example
Nice to have
• Email: lorna@rbtonalartsroom.example
Should not have
• Any instruments on the card other than piano. Instrument pix is not a necessity.

```html
<!DOCTYPE html>
<html lang="en">
<head>
<meta charset="utf-8">
<title>R&amp;B Music Studio – Business Card</title>
<link rel="stylesheet" href="https://fonts.googleapis.com/css2?family=Josefin+Sans:wght@300&family=Open+Sans:wght@400;600;700&display=swap">
<style>
  :root {
    --backdrop: #2b2b2b;
    --card: #151515;
    --card-panel: #1c1c1c;
    --ink: #ffffff;
    --ink-soft: #d6d6d6;
  }
  * { margin: 0; padding: 0; box-sizing: border-box; }
  html, body {
    width: 1200px;
    height: 900px;
    overflow: hidden;
    background: var(--backdrop);
    font-family: "Open Sans", Arial, sans-serif;
  }
  .canvas {
    position: relative;
    width: 1200px;
    height: 900px;
    display: flex;
    align-items: center;
    justify-content: center;
    gap: 40px;
  }
  .card {
    position: relative;
    width: 540px;
    height: 310px;
    background: var(--card);
    border-radius: 22px;
    color: var(--ink);
    overflow: hidden;
  }
  /* Front side: brand on the left, owner and contact details on the right */
  .card-front { display: flex; }
  .front-brand {
    flex: 0 0 290px;
    display: flex;
    align-items: center;
    justify-content: center;
  }
  .brand-name {
    font-weight: 600;
    font-size: 68px;
    letter-spacing: 2px;
    color: var(--ink);
    white-space: nowrap;
  }
  .front-details {
    flex: 1;
    background: var(--card-panel);
    display: flex;
    flex-direction: column;
    justify-content: center;
    padding-left: 30px;
    padding-right: 14px;
    line-height: 1.45;
  }
  .owner-name {
    font-weight: 700;
    font-size: 16px;
    white-space: nowrap;
  }
  .owner-role,
  .studio-location,
  .contact-line {
    font-weight: 400;
    font-size: 13px;
    color: var(--ink-soft);
    white-space: nowrap;
  }
  .owner-role { margin-top: 4px; }
  .contact-list { margin-top: 12px; }
  /* Back side: centred brand */
  .card-back {
    display: flex;
    flex-direction: column;
    align-items: center;
    justify-content: center;
    gap: 4px;
  }
  .card-back .brand-name { font-size: 64px; }
  .studio-tagline {
    font-family: "Josefin Sans", "Open Sans", sans-serif;
    font-weight: 300;
    font-size: 40px;
    letter-spacing: 1px;
  }
</style>
</head>
<body>
  <main class="canvas">
    <section class="card card-front" aria-label="Business card front">
      <div class="front-brand">
        <span class="brand-name">R&amp;B</span>
      </div>
      <div class="front-details">
        <p class="owner-name">Lorna P. Quist</p>
        <p class="owner-name">Oren M. Castaldi</p>
        <p class="owner-role">Owners</p>
        <p class="studio-location">Harlow Falls, NY</p>
        <div class="contact-list">
          <p class="contact-line">(555) 817-4062</p>
          <p class="contact-line">www.rbtonalartsroom.example</p>
          <p class="contact-line">lorna@rbtonalartsroom.example</p>
        </div>
      </div>
    </section>

    <section class="card card-back" aria-label="Business card back">
      <span class="brand-name">R&amp;B</span>
      <span class="studio-tagline">Music Studio</span>
    </section>
  </main>
</body>
</html>
```